BOLD & MINIMALIST DESIGN NEEDED

We want a very bold but minimalistic business card design that is impactful and utilizes both sides of the business card. Our current logo is included for your use.

We want bold fonts and good use of negative space. We don't want the logo to overpower the design.

Target Market(s)

Professionals who are building new commercial buildings.

Industry/Entity Type

Construction

Contact Information for Business Card

Name, Title, email, office phone, cell phone, website

Font styles to use
Serif
Sans Serif

Requirements
Must have
• Bold design!

```html
<!DOCTYPE html>
<html lang="en">
<head>
<meta charset="utf-8">
<title>Ridgeway Design + Build — Business Card</title>
<link rel="stylesheet" href="https://fonts.googleapis.com/css2?family=Montserrat:wght@700;800&family=Questrial&display=swap">
<style>
  :root {
    --ink: #111111;
    --muted: #6b6b6b;
    --green: #6cc04a;
    --card: #f7f7f7;
    --card-edge: #e6e6e6;
    --backdrop: #2b2b2b;
    --photo-gap: #ffffff;
  }
  * { box-sizing: border-box; margin: 0; padding: 0; }
  html, body {
    width: 1200px; height: 900px; overflow: hidden;
    background: var(--backdrop);
  }
  .stage { position: relative; width: 1200px; height: 900px; }

  .card {
    position: absolute; width: 700px; height: 400px;
    background: linear-gradient(135deg, #ffffff 0%, var(--card) 60%, #ececec 100%);
    box-shadow: 0 18px 40px rgba(0,0,0,.45);
    overflow: hidden;
  }
  .card--front { left: 70px; top: 35px; }
  .card--back  { left: 430px; top: 465px; }

  /* Wordmark */
  .wordmark { position: absolute; display: flex; flex-direction: column; align-items: flex-start; }
  .wordmark__row { display: flex; align-items: center; gap: 12px; }
  .wordmark__square { width: 30px; height: 30px; background: var(--green); }
  .wordmark__name {
    font-family: "Montserrat", sans-serif; font-weight: 800;
    font-size: 40px; letter-spacing: 1px; color: var(--ink); line-height: 1;
  }
  .wordmark__sub {
    margin-top: 8px; padding-top: 6px; border-top: 2px solid var(--ink);
    font-family: "Questrial", sans-serif; font-size: 15px; letter-spacing: 6px;
    color: var(--ink); align-self: stretch; text-align: center;
  }
  .card--front .wordmark { left: 50px; top: 160px; }
  .card--back .wordmark { right: 40px; top: 40px; }
  .card--back .wordmark__name { font-size: 34px; }
  .card--back .wordmark__square { width: 26px; height: 26px; }

  /* Project photo grid */
  .gallery {
    position: absolute; left: 350px; top: 0; width: 350px; height: 400px;
    display: grid; grid-template-columns: 1fr 1fr; grid-template-rows: 1.1fr 1fr 0.9fr;
    gap: 6px; background: var(--photo-gap); padding: 0 0 0 6px;
  }
  .gallery__tile { width: 100%; height: 100%; }
  .tile--interior { background: linear-gradient(160deg, #3a2e25, #8a6a48 60%, #b58c5e); }
  .tile--exterior { background: linear-gradient(180deg, #6fa3d8 0%, #b0573a 45%, #9aa3ab 100%); }
  .tile--lounge   { background: linear-gradient(150deg, #2c1b12, #a0612f 55%, #d69a4e); }
  .tile--lobby    { background: linear-gradient(170deg, #e9e9e9, #5fb8c9 40%, #9b8c7c); grid-row: span 2; }
  .tile--storefront { background: linear-gradient(180deg, #d9dde2, #8a949e 55%, #4b5259); }

  /* Back side details */
  .faint-mark {
    position: absolute; right: 50px; bottom: 40px; width: 170px; height: 170px;
    background: linear-gradient(135deg, rgba(108,192,74,.14), rgba(0,0,0,.05));
  }
  .contact {
    position: absolute; left: 55px; top: 150px;
    font-family: "Questrial", sans-serif; color: var(--muted); font-size: 17px; line-height: 1.35;
  }
  .contact__name {
    font-family: "Montserrat", sans-serif; font-weight: 800; font-size: 24px; color: var(--ink);
  }
  .contact__title { font-size: 19px; margin-bottom: 2px; }
  .contact__line { display: flex; align-items: center; gap: 9px; }
  .contact__address { margin: 22px 0 22px; }
  .contact__icon { width: 16px; height: 16px; flex: none; }
  .accent { color: var(--green); }
</style>
</head>
<body>
<main class="stage">

  <section class="card card--front" aria-label="Card front">
    <div class="wordmark">
      <div class="wordmark__row">
        <span class="wordmark__square"></span>
        <span class="wordmark__name">RIDGEWAY</span>
      </div>
      <span class="wordmark__sub">DESIGN + BUILD</span>
    </div>
    <div class="gallery">
      <div class="gallery__tile tile--interior" role="img" aria-label="Photo of a finished commercial interior with wood tables"></div>
      <div class="gallery__tile tile--exterior" role="img" aria-label="Photo of a building exterior with timber cladding"></div>
      <div class="gallery__tile tile--lounge" role="img" aria-label="Photo of a warmly lit restaurant space"></div>
      <div class="gallery__tile tile--lobby" role="img" aria-label="Photo of a lobby with wood-panel wall"></div>
      <div class="gallery__tile tile--storefront" role="img" aria-label="Photo of a retail storefront and parking lot"></div>
    </div>
  </section>

  <section class="card card--back" aria-label="Card back">
    <div class="faint-mark"></div>
    <div class="wordmark">
      <div class="wordmark__row">
        <span class="wordmark__square"></span>
        <span class="wordmark__name">RIDGEWAY</span>
      </div>
      <span class="wordmark__sub">DESIGN + BUILD</span>
    </div>

    <div class="contact">
      <p class="contact__name">Jonah Whitfield</p>
      <p class="contact__title">Founder</p>
      <p class="contact__line">
        <svg class="contact__icon" viewBox="0 0 16 16"><rect x="4" y="1" width="8" height="14" rx="1.5" fill="none" stroke="#6cc04a" stroke-width="1.6"/><circle cx="8" cy="12.3" r=".9" fill="#6cc04a"/></svg>
        555-214-9037
      </p>
      <p class="contact__address">1420 Cedar Hollow Rd.<br>Pine Bluff, GA 30999</p>
      <p class="contact__line">
        <svg class="contact__icon" viewBox="0 0 16 16"><path d="M3 2h3l1.2 3-1.7 1.2a8 8 0 0 0 4.3 4.3L11 8.8l3 1.2v3c0 .6-.5 1-1 1A12 12 0 0 1 2 3c0-.5.4-1 1-1z" fill="#6cc04a"/></svg>
        555-630-4100
      </p>
      <p class="contact__line">
        <svg class="contact__icon" viewBox="0 0 16 16"><rect x="1" y="3" width="14" height="10" fill="#6cc04a"/><path d="M1 3l7 6 7-6" fill="none" stroke="#fff" stroke-width="1.3"/></svg>
        <span>info@<span class="accent">r-d-b</span>.com</span>
      </p>
      <p class="contact__line">
        <svg class="contact__icon" viewBox="0 0 16 16"><g fill="none" stroke="#6cc04a" stroke-width="1.3"><circle cx="8" cy="8" r="6.5"/><ellipse cx="8" cy="8" rx="2.8" ry="6.5"/><path d="M1.5 8h13M2.5 4.8h11M2.5 11.2h11"/></g></svg>
        <span>www.<span class="accent">r-d-b</span>.com</span>
      </p>
    </div>
  </section>

</main>
</body>
</html>
```